Black Matte card with samurai logo which I would like it to be textured and company name on one side and on the other side I would like the company information with the reno (Face logo) Sushi logo. Double Sided card.

majority customers are University students, University sororities and fraternities.

It Company

Reno Sushi
317 W. Harlow Ave
Tucson, AZ 85042
Phone (520)413-6271
Fax (520)357-1846
E-mail: Renosushidesert@mailbox-example.com
FB: Renosushidesert
Twitter: Renosushidesert

• Present Normal

```html
<!DOCTYPE html>
<html lang="en">
<head>
<meta charset="utf-8">
<title>Reno Sushi – Business Card</title>
<link rel="stylesheet" href="https://fonts.googleapis.com/css2?family=Source+Sans+3:wght@400;600&display=swap">
<style>
  :root {
    --backdrop: #e9e6e1;
    --card-black: #141414;
    --card-charcoal: #2c2c2c;
    --card-white: #ffffff;
    --brand-red: #c4262e;
    --deep-red: #8e1820;
    --ink: #3a3a3a;
    --rule: #cfcfcf;
    --art-dark: #2a2a2a;
    --art-red: #a8232a;
  }
  * { box-sizing: border-box; margin: 0; padding: 0; }
  html, body { width: 1200px; height: 1120px; overflow: hidden; }
  body {
    background: var(--backdrop);
    font-family: "Source Sans 3", "Helvetica Neue", Arial, sans-serif;
    position: relative;
  }
  .card {
    position: absolute;
    width: 881px;
    height: 503px;
    border-radius: 26px;
    overflow: hidden;
    box-shadow: 0 2px 6px rgba(0,0,0,.18);
  }
  /* Front side */
  .card-front {
    left: 292px; top: 25px;
    background:
      repeating-linear-gradient(180deg, rgba(255,255,255,.035) 0 2px, transparent 2px 9px),
      linear-gradient(180deg, var(--card-charcoal), var(--card-black) 55%, var(--card-charcoal));
  }
  .card-front .emblem {
    position: absolute;
    left: 286px; top: 43px;
    width: 291px; height: 280px;
    border-radius: 12px;
    background: radial-gradient(circle at 50% 45%, #4a4a4a, var(--art-dark) 60%, rgba(168,35,42,.55));
  }
  .card-front .brand-name {
    position: absolute;
    left: 0; right: 0; top: 352px;
    text-align: center;
    font-size: 70px;
    font-weight: 400;
    color: var(--brand-red);
    letter-spacing: 1px;
  }
  /* Back side */
  .card-back {
    left: 99px; top: 580px;
    background: var(--card-white);
    border: 1px solid #999;
  }
  .card-back .emblem {
    position: absolute;
    left: 120px; top: 48px;
    width: 201px; height: 191px;
    border-radius: 10px;
    background: radial-gradient(circle at 50% 45%, #555, var(--art-dark) 60%, rgba(168,35,42,.6));
  }
  .card-back .brand-name {
    position: absolute;
    left: 110px; width: 221px; top: 246px;
    text-align: center;
    font-size: 50px;
    line-height: 46px;
    font-weight: 400;
    color: var(--brand-red);
  }
  .divider {
    position: absolute;
    left: 386px; top: 121px;
    width: 1px; height: 196px;
    background: var(--rule);
  }
  .contact {
    position: absolute;
    left: 413px; top: 130px;
    list-style: none;
    color: var(--ink);
    font-size: 22px;
  }
  .contact li {
    display: flex; align-items: center;
    height: 34px;
  }
  .contact svg { width: 18px; height: 18px; margin-right: 14px; flex: none; }
  .address {
    position: absolute;
    left: 413px; top: 244px;
    color: var(--ink);
    font-size: 22px;
    line-height: 32px;
    font-style: normal;
  }
  .swoosh { position: absolute; left: 0; top: 0; width: 881px; height: 503px; }
  .social {
    position: absolute;
    left: 603px; top: 416px;
    list-style: none;
    color: #fff;
    font-size: 22px;
  }
  .social li { display: flex; align-items: center; height: 30px; }
  .social .mark {
    width: 20px; height: 20px; margin-right: 10px;
    background: #5a82c8; border-radius: 3px;
  }
</style>
</head>
<body>

<section class="card card-front" aria-label="Card front">
  <div class="emblem" role="img" aria-label="Samurai mascot holding a sword and a fish"></div>
  <div class="brand-name">reno sushi</div>
</section>

<section class="card card-back" aria-label="Card back">
  <svg class="swoosh" viewBox="0 0 881 503" aria-hidden="true">
    <path d="M0,428 C300,388 600,318 881,392" fill="none" stroke="var(--deep-red)" stroke-width="7"/>
    <path d="M0,446 C300,404 560,352 881,398 L881,408 C560,372 300,428 0,474 Z" fill="var(--brand-red)"/>
    <path d="M0,484 C300,444 560,384 881,412 L881,503 L0,503 Z" fill="var(--card-black)"/>
  </svg>

  <div class="emblem" role="img" aria-label="Samurai mascot holding a sword and a fish"></div>
  <div class="brand-name">reno<br>sushi</div>

  <div class="divider"></div>

  <ul class="contact">
    <li>
      <svg viewBox="0 0 20 20"><circle cx="10" cy="10" r="8.5" fill="none" stroke="var(--brand-red)" stroke-width="1.6"/><path d="M7 5.5l2 2-1 1.5c.6 1.3 1.6 2.3 3 3l1.5-1 2 2-1.3 1.5C9.5 14 6 10.5 5.5 6.8z" fill="var(--brand-red)"/></svg>
      (520)413-6271
    </li>
    <li>
      <svg viewBox="0 0 20 20"><rect x="5" y="1.5" width="10" height="17" rx="2" fill="var(--brand-red)"/><rect x="7" y="4" width="6" height="6" fill="#fff"/><rect x="7" y="12" width="6" height="4" fill="#fff" opacity=".7"/></svg>
      (520)357-1846
    </li>
    <li>
      <svg viewBox="0 0 20 20"><rect x="1.5" y="5" width="17" height="11" rx="1.5" fill="var(--brand-red)"/><path d="M2 6l8 6 8-6" fill="none" stroke="#fff" stroke-width="1.5"/></svg>
      Renosushidesert@mailbox-example.com
    </li>
  </ul>

  <address class="address">
    Reno Sushi 317 W. Harlow Ave Tucson<br>AZ 85042
  </address>

  <ul class="social">
    <li><span class="mark"></span>Renosushidesert</li>
    <li><span class="mark"></span>Renosushidesert</li>
  </ul>
</section>

</body>
</html>
```